K7 Services business card design contest. Use logo and create a professional layout.

See attached sample. Please sharpen all text and images, don't want any pix-elated content. We are looking for a clean look that quickly provides the information need. Please include our information provided on the sample card. Please feel free to offer any design changes. Please only user the colors provided: #2D3539 & #FFA500. Do not prefer any images other than the K7 Logo

Target Market(s)

Construction, Architects, General Contractors, residential

Industry/Entity Type

Business

Contact Information for Business Card

Company logo, Name, email, fax & phone

Font styles to use
Other font styles liked:
• Josefin Slab

Requirements
Must have
• Name
• Phone & Fax #'s
• address
• Logo
• Website url: www.kq7services.example
Nice to have
• Font Colors #2D3539 & #FFA400
• We prefer a white background.

```html
<!DOCTYPE html>
<html lang="en">
<head>
<meta charset="utf-8">
<title>K7 Services – Business Card</title>
<link href="https://fonts.googleapis.com/css2?family=Montserrat:wght@400;500;600;700&display=swap" rel="stylesheet">
<style>
  :root {
    --ink: #2D3539;
    --accent: #FFA500;
    --paper: #FFFFFF;
    --backdrop: #E4E4E4;
    --muted: #3c4448;
  }
  * { box-sizing: border-box; margin: 0; padding: 0; }
  html, body {
    width: 1200px; height: 852px; overflow: hidden;
    background: var(--backdrop);
    font-family: "Montserrat", Arial, sans-serif;
    color: var(--ink);
  }
  .stage { position: relative; width: 1200px; height: 852px; }
  .card {
    position: absolute;
    width: 525px; height: 300px;
    background: var(--paper);
    border-radius: 14px;
    overflow: hidden;
    box-shadow: 0 6px 18px rgba(0,0,0,0.18);
  }
  .card--front { left: 50px; top: 120px; }
  .card--back  { left: 625px; top: 432px; }

  .brand { display: flex; align-items: center; gap: 12px; }
  .brand__dot { width: 18px; height: 18px; border-radius: 50%; background: var(--ink); }
  .brand__name { font-weight: 700; color: var(--ink); letter-spacing: -0.5px; }

  .card--front .brand {
    position: absolute; left: 0; right: 0; top: 0; bottom: 0;
    justify-content: center;
  }
  .card--front .brand__name { font-size: 46px; }
  .card--front .brand__dot { width: 28px; height: 28px; }

  .card--back .brand { position: absolute; left: 34px; top: 46px; }
  .card--back .brand__name { font-size: 28px; }

  .contact { position: absolute; left: 285px; top: 40px; }
  .contact__name { color: var(--accent); font-size: 16px; font-weight: 500; }
  .contact__role { font-size: 11px; font-weight: 500; margin-top: 3px; color: var(--muted); }
  .contact__list { list-style: none; margin-top: 14px; font-size: 10.5px; line-height: 1.6; color: var(--muted); }
  .contact__list li { display: flex; align-items: center; gap: 7px; }
  .contact__list svg { width: 11px; height: 11px; flex: none; fill: var(--accent); }
  .contact__address { margin-top: 4px; padding-left: 18px; font-size: 10.5px; line-height: 1.5; color: var(--muted); }

  .services {
    position: absolute; left: 34px; bottom: 34px;
    color: var(--accent); font-size: 12px; letter-spacing: 0.5px; font-weight: 500;
  }
  .band { position: absolute; left: 0; right: 0; bottom: 0; height: 9px; display: flex; }
  .band__accent { flex: 1; background: var(--accent); }
  .band__ink { width: 70px; background: var(--ink); }
</style>
</head>
<body>
<main class="stage">
  <section class="card card--front" aria-label="Card front">
    <div class="brand">
      <span class="brand__dot"></span>
      <span class="brand__name">K7 Services</span>
    </div>
  </section>

  <section class="card card--back" aria-label="Card back">
    <div class="brand">
      <span class="brand__dot"></span>
      <span class="brand__name">K7 Services</span>
    </div>

    <div class="contact">
      <p class="contact__name">Daniel R. Hollis, MBA</p>
      <p class="contact__role">Director of Operations</p>
      <ul class="contact__list">
        <li>
          <svg viewBox="0 0 24 24" aria-hidden="true"><path d="M6.6 10.8a15 15 0 0 0 6.6 6.6l2.2-2.2a1 1 0 0 1 1-.25 11.4 11.4 0 0 0 3.6.6 1 1 0 0 1 1 1V20a1 1 0 0 1-1 1A17 17 0 0 1 3 4a1 1 0 0 1 1-1h3.5a1 1 0 0 1 1 1c0 1.25.2 2.45.6 3.6a1 1 0 0 1-.25 1z"/></svg>
          (555) 014 - 2731
        </li>
        <li>
          <svg viewBox="0 0 24 24" aria-hidden="true"><path d="M6 2h9l3 3v5H6zM4 11h16a2 2 0 0 1 2 2v7a2 2 0 0 1-2 2H4a2 2 0 0 1-2-2v-7a2 2 0 0 1 2-2zm2 3v2h6v-2z"/></svg>
          (555) 018 - 6642
        </li>
        <li>
          <svg viewBox="0 0 24 24" aria-hidden="true"><path d="M12 2a10 10 0 1 0 0 20 10 10 0 0 0 0-20zm6.9 6h-3a15 15 0 0 0-1.3-3.9A8 8 0 0 1 18.9 8zM12 4c.8 1.2 1.5 2.5 1.9 4h-3.8c.4-1.5 1.1-2.8 1.9-4zM4.3 14a8 8 0 0 1 0-4h3.4a16 16 0 0 0 0 4zm.8 2h3a15 15 0 0 0 1.3 3.9A8 8 0 0 1 5.1 16zm3-8h-3a8 8 0 0 1 4.3-3.9C8.9 5.3 8.4 6.6 8.1 8zM12 20c-.8-1.2-1.5-2.5-1.9-4h3.8c-.4 1.5-1.1 2.8-1.9 4zm2.3-6H9.7a14 14 0 0 1 0-4h4.6a14 14 0 0 1 0 4zm.3 5.9c.6-1.2 1-2.5 1.3-3.9h3a8 8 0 0 1-4.3 3.9zm1.7-5.9a16 16 0 0 0 0-4h3.4a8 8 0 0 1 0 4z"/></svg>
          www.kq7services.example
        </li>
      </ul>
      <p class="contact__address">2140 Maple Ridge Road, Suite<br>210-118 Fairview, Georgia, 30099</p>
    </div>

    <p class="services">DRONE | WEBCAM | VIDEO</p>

    <div class="band">
      <span class="band__accent"></span>
      <span class="band__ink"></span>
    </div>
  </section>
</main>
</body>
</html>
```